KRT Project Signage

Need a sign to be displayed in the front of properties currently under Construction or Renovation to advertise our company information. Need it to be Professional and Contemporary. We are a Design/Build Construction Company. Information should include Company Name, email, website, phone number. Attached: Logo and company brochure, also included and inspiration images

```html
<!DOCTYPE html>
<html lang="en">
<head>
<meta charset="utf-8">
<title>KRT Project Signage</title>
<link rel="stylesheet" href="https://fonts.googleapis.com/css2?family=Bebas+Neue&family=Montserrat:wght@500;600&family=Poppins:wght@400;600;700&display=swap">
<style>
  :root {
    --ink: #262626;
    --yellow: #f2e52e;
    --panel: #f4f4f4;
    --panel-shade: #e6e6e6;
    --text: #3a3a3a;
    --white: #ffffff;
  }
  * { margin: 0; padding: 0; box-sizing: border-box; }
  html, body { width: 1200px; height: 3390px; overflow: hidden; background: var(--white); }
  .canvas { position: relative; width: 1200px; height: 3390px; background: var(--white); }
  .sign {
    position: absolute; left: 100px; top: 945px; width: 1000px; height: 1500px;
    background: var(--panel); overflow: hidden;
    box-shadow: 0 6px 24px rgba(0,0,0,0.12);
    font-family: "Poppins", sans-serif; color: var(--text);
  }
  .sign__backdrop {
    position: absolute; left: 0; top: 302px; width: 100%; height: 1084px;
    background: linear-gradient(180deg, var(--panel) 0%, var(--panel-shade) 45%, var(--panel) 100%);
    opacity: 0.7;
  }
  .sign__header {
    position: absolute; left: 0; top: 0; width: 100%; height: 302px;
    background: var(--ink); text-align: center;
  }
  .sign__name {
    font-family: "Bebas Neue", sans-serif; color: var(--white);
    font-size: 178px; line-height: 1; letter-spacing: 1px; padding-top: 44px;
  }
  .sign__trade {
    font-family: "Montserrat", sans-serif; font-weight: 600; color: var(--yellow);
    font-size: 66px; line-height: 1; letter-spacing: 9px; margin-top: 2px;
  }
  .brand {
    position: absolute; left: 0; top: 392px; width: 100%;
    display: flex; justify-content: center; align-items: center; gap: 22px;
  }
  .brand__dot { width: 60px; height: 60px; border-radius: 50%; background: var(--yellow); }
  .brand__name {
    font-family: "Poppins", sans-serif; font-weight: 600; font-size: 56px;
    color: var(--ink); letter-spacing: 2px;
  }
  .icon {
    position: absolute; left: 464px; width: 72px; height: 72px;
    border-radius: 50%; background: var(--yellow);
    display: flex; align-items: center; justify-content: center;
  }
  .icon svg { width: 40px; height: 40px; }
  .line {
    position: absolute; left: 0; width: 100%; text-align: center;
    font-size: 43px; line-height: 52px; color: var(--text);
  }
  .office {
    position: absolute; left: 0; top: 1220px; width: 100%;
    display: flex; justify-content: center; align-items: center; gap: 34px;
    font-weight: 700; font-size: 66px; color: var(--ink);
  }
  .office__icon {
    width: 84px; height: 84px; border-radius: 50%; background: var(--yellow);
    display: flex; align-items: center; justify-content: center;
  }
  .office__icon svg { width: 50px; height: 50px; }
  .sign__band {
    position: absolute; left: 0; top: 1386px; width: 100%; height: 114px; background: var(--yellow);
  }
  .mobile {
    position: absolute; left: 80px; top: 1336px; width: 840px; height: 116px;
    background: var(--ink); border-radius: 26px;
    display: flex; align-items: center; justify-content: center; gap: 40px;
    color: var(--white); font-weight: 700; font-size: 96px; line-height: 1;
  }
  .mobile svg { width: 80px; height: 80px; }
</style>
</head>
<body>
<div class="canvas">
  <div class="sign">
    <div class="sign__backdrop" role="img" aria-label="Faint photo of a construction interior behind the contact details"></div>

    <header class="sign__header">
      <div class="sign__name">DORIAN VALE</div>
      <div class="sign__trade">DESIGN &amp; BUILDER</div>
    </header>

    <div class="brand">
      <span class="brand__dot"></span>
      <span class="brand__name">KRT CONSTRUCTION</span>
    </div>

    <div class="icon" style="top:612px">
      <svg viewBox="0 0 24 24"><path d="M12 2a7 7 0 0 0-7 7c0 5 7 11 7 11s7-6 7-11a7 7 0 0 0-7-7zm0 9.5A2.5 2.5 0 1 1 12 6.5a2.5 2.5 0 0 1 0 5z" fill="#262626"/><path d="M5 21h14" stroke="#262626" stroke-width="2"/></svg>
    </div>
    <p class="line" style="top:706px">1450 Harbor Point Blvd., Ste. 310 Coral<br>Bay, FL 33000</p>

    <div class="icon" style="top:852px">
      <svg viewBox="0 0 24 24"><rect x="3" y="6" width="18" height="12" rx="1.5" fill="#262626"/><path d="M3.5 6.5 12 13l8.5-6.5" stroke="#f2e52e" stroke-width="1.6" fill="none"/></svg>
    </div>
    <p class="line" style="top:946px">info@krtconstruction.com</p>

    <div class="icon" style="top:1033px">
      <svg viewBox="0 0 24 24" fill="none" stroke="#262626" stroke-width="1.8"><circle cx="12" cy="12" r="9" fill="#262626"/><g stroke="#f2e52e" stroke-width="1.2"><ellipse cx="12" cy="12" rx="4" ry="9"/><path d="M3 12h18M5 7.5h14M5 16.5h14M12 3v18"/></g></svg>
    </div>
    <p class="line" style="top:1126px">www.krtconstruction.com</p>

    <div class="office">
      <span>Office</span>
      <span class="office__icon">
        <svg viewBox="0 0 24 24"><path d="M6.6 3.5 9 3l1.5 4.2-2 1.3a11 11 0 0 0 5 5l1.3-2L19 13l-.5 2.4A3 3 0 0 1 15.6 18C9.6 17.4 6 13.8 5.5 8A3 3 0 0 1 6.6 3.5z" fill="#262626"/><path d="M14 4a6 6 0 0 1 5 5M14 7a3 3 0 0 1 2.5 2.5" stroke="#262626" stroke-width="1.6" fill="none"/></svg>
      </span>
      <span>555.014.2280</span>
    </div>

    <div class="sign__band"></div>
    <div class="mobile">
      <svg viewBox="0 0 24 24"><path d="M6.6 3.5 9 3l1.5 4.2-2 1.3a11 11 0 0 0 5 5l1.3-2L19 13l-.5 2.4A3 3 0 0 1 15.6 18C9.6 17.4 6 13.8 5.5 8A3 3 0 0 1 6.6 3.5z" fill="#f2e52e"/><path d="M14 4a6 6 0 0 1 5 5M14 7a3 3 0 0 1 2.5 2.5" stroke="#f2e52e" stroke-width="1.6" fill="none"/></svg>
      <span>555.019.3746</span>
    </div>
  </div>
</div>
</body>
</html>
```